Plumberry Brochure - Tri Fold

Need to design a brochure for my business. Our colors are Pink/Black/White. I have included a new ad that I like the colors. This is a Cake Business that features gourmet cupcakes(retail and special order) , Custom Cakes for special occasions, Our retail shop which features our cupcakes, gelato, coffee, tea.

Focus should be on: Custom Cupcake orders for meetings, groups, schools, etc (catering).. Custom Cakes (special events - weddings, birthdays etc., Retail Sales (cupcakes, gelato, coffee, tea espresso at our Shop, Decorating Classes/birthday parties.

See our sample brochure and advertisements for colors and some content

Like to have a map on the back with our address, website, phone number

We will guaranty payment

Target Market(s)

People ordering cupcakes for meetings, parties, events, school functions
Retail customers coming to our shop to enjoy our products
People ordering custom cakes for their special occasions
Cake Decorating classes/Birthday parties

Industry/Entity Type

Retail

Font styles to use
Serif
Sans Serif

Colors
ffffff
e567a6
1b1b1b
ebebeb

Requirements
Must have
• Custom Cupcake orders
Custom Cakes
Retail Customers

website
telephone numbers
facebook page
address
hours of operation
Nice to have
• The custom orders are the priority
followed by the retail
followed by cake decorating classes/birthday parties

```html
<!DOCTYPE html>
<html lang="en">
<head>
<meta charset="utf-8">
<title>The Plumberry Cake House – Tri-Fold Brochure</title>
<link rel="stylesheet" href="https://fonts.googleapis.com/css2?family=Questrial&family=Great+Vibes&display=swap">
<style>
:root{
  --pink:#e567a6;
  --pink-deep:#d94f93;
  --pink-soft:#f6d3e5;
  --pink-pale:#fbeaf3;
  --ink:#1b1b1b;
  --white:#ffffff;
  --grey:#ebebeb;
  --backdrop:#cfcfcf;
  --sans:"Questrial", Arial, sans-serif;
  --script:"Great Vibes", cursive;
}
*{box-sizing:border-box;margin:0;padding:0}
html,body{width:1000px;height:1200px;overflow:hidden}
body{background:var(--backdrop);font-family:var(--sans);color:var(--ink)}

.sheet{position:absolute;left:40px;width:920px;height:550px;display:flex;background:var(--white);box-shadow:0 6px 18px rgba(0,0,0,.25)}
.sheet--inside{top:28px}
.sheet--outside{top:618px}

.panel{position:relative;width:calc(100% / 3);height:100%;overflow:hidden;display:flex;flex-direction:column;align-items:center;
  background:linear-gradient(90deg,var(--pink-pale),var(--white) 50%,var(--pink-pale));padding:0 16px}
.panel--cover{background:linear-gradient(180deg,#f3b3d2,var(--pink) 45%,#ec84b8)}

.band{position:absolute;left:0;right:0;height:16px;background:var(--pink)}
.band--top{top:14px}
.band--bottom{bottom:10px;height:20px}

.body-text{font-size:10.5px;line-height:1.32;text-align:center;color:var(--ink)}
.body-text + .body-text{margin-top:6px}

.logo{display:flex;align-items:center;gap:6px;margin-top:44px}
.logo__dot{width:14px;height:14px;border-radius:50%;background:var(--pink);flex:none}
.logo__name{font-family:var(--sans);font-size:17px;color:var(--ink);letter-spacing:.5px;white-space:nowrap}

.photo{border:3px solid var(--white);box-shadow:0 1px 3px rgba(0,0,0,.3)}
.icon-cupcake{width:34px;height:38px;flex:none;border-radius:14px 14px 4px 4px;background:linear-gradient(180deg,#f08cbd,#f4b46a)}

.ribbon{align-self:stretch;margin:0 -16px;background:var(--pink);color:var(--white);font-family:var(--script);text-align:center;
  clip-path:polygon(0 0,100% 0,94% 50%,100% 100%,0 100%,6% 50%)}

.script{font-family:var(--script)}
.tagline-art{width:190px;height:34px;border-radius:4px;background:linear-gradient(90deg,var(--pink-soft),#f2b8d4,var(--pink-soft))}

.list{list-style:none;font-size:10.5px;line-height:1.45;text-align:center}
.list li::before{content:"";display:inline-block;width:7px;height:7px;border-radius:50%;background:var(--pink);margin-right:4px}

.contact-strip{position:absolute;left:0;right:0;bottom:10px;background:var(--pink);color:var(--white);font-size:11px;text-align:center;padding:5px 0;line-height:1.4}
</style>
</head>
<body>

<section class="sheet sheet--inside">
  <article class="panel panel--story">
    <div class="band band--top"></div>
    <div class="logo"><span class="logo__dot"></span><span class="logo__name">The Plumberry Cake House</span></div>
    <div style="display:flex;gap:8px;margin-top:12px;align-items:flex-start">
      <div class="icon-cupcake" role="img" aria-label="Cupcake illustration"></div>
      <p class="body-text" style="text-align:left">was founded in 2014 by Helen Dorsey and Paul Warren. Loving all things sweet growing up, Helen developed a passion for creating and baking all kinds of special treats including cakes, cupcakes, cookies and special chocolates. She and Paul found the ideal location to implement their vision of a neighborhood spot where someone could stop in for a treat at all hours of the day.</p>
    </div>
    <div class="photo" role="img" aria-label="Photo of the pink shop interior with display shelves and counter" style="width:100%;height:120px;margin-top:10px;background:linear-gradient(135deg,#e9a3c6,#f7e3ee 60%,#cfc4c9)"></div>
    <p class="body-text" style="margin-top:10px">They wanted a friendly place for The Plumberry Cake House will serve over 15 types of Gourmet Cupcakes, and other special treats at their beautifully remodeled storefront in Harbor Pines Center. All the cupcakes will have unique tastes and be beautifully designed and decorated by Helen "The Cake Maker". They will use only using the best ingredients and everything will be baked fresh each day. Our shop will be open for you to stop in for an afternoon snack, a before or after dinner treat, or a night craving. We will offer all our customers that want to sit down and enjoy our shop free Wifi!</p>
    <div class="band band--bottom"></div>
  </article>

  <article class="panel panel--cakes">
    <div style="display:flex;gap:10px;margin-top:34px;align-self:stretch;align-items:flex-start">
      <div style="width:125px">
        <div class="script" style="background:var(--pink-soft);border:2px solid var(--ink);font-size:16px;line-height:1.05;text-align:center;padding:4px">Custom Cakes by our Amazing Decorator, <b style="font-size:19px">Greta.</b></div>
        <div class="photo" role="img" aria-label="Photo of the decorator with a tray of cupcakes" style="height:70px;margin-top:4px;background:linear-gradient(135deg,#b9a3ad,#f0c7dc)"></div>
      </div>
      <div class="body-text" style="flex:1;padding-top:14px">
        <p>We provide extraordinary cakes for every special occasion.</p>
        <p style="margin-top:10px">All cakes are made fresh from scratch. We collaborate with our clients to suite the occasion.</p>
      </div>
    </div>
    <div style="margin-top:16px;background:var(--pink-soft);border:3px solid var(--white);box-shadow:0 0 0 1px var(--pink);padding:6px 10px;width:92%">
      <p class="script" style="font-size:21px;text-align:center">We design cakes for:</p>
      <ul class="list" style="display:grid;grid-template-columns:1fr 1fr;gap:0 6px;text-align:left">
        <li>Weddings</li><li>Birthdays</li><li>Anniversaries</li><li>Bridal Showers</li><li>Baby Showers</li><li>Special Occasions</li>
      </ul>
    </div>
    <div style="display:grid;grid-template-columns:repeat(4,1fr);grid-template-rows:64px 64px;gap:3px;width:100%;margin-top:10px">
      <div role="img" aria-label="Photo of a cupcake bouquet" style="background:linear-gradient(135deg,#e7c24a,#d95f8e)"></div>
      <div role="img" aria-label="Photo of a blue gift-box tiered cake" style="background:linear-gradient(135deg,#8fc6c9,#e9e4e2)"></div>
      <div role="img" aria-label="Photo of a black themed cake" style="background:linear-gradient(135deg,#2a2424,#8a6d66)"></div>
      <div role="img" aria-label="Photo of a green novelty cake" style="background:linear-gradient(135deg,#5c9a62,#2d3a2e)"></div>
      <div role="img" aria-label="Photo of pink cake pops" style="grid-column:1/3;background:linear-gradient(135deg,#e06b9e,#f5c6dc)"></div>
      <div role="img" aria-label="Photo of a giant pink cupcake cake" style="grid-column:3/5;background:linear-gradient(135deg,#f3b4cf,#7a4a3a)"></div>
    </div>
    <div class="tagline-art" role="img" aria-label="Hand-lettered tagline" style="margin-top:10px"></div>
    <div class="band band--bottom"></div>
  </article>

  <article class="panel panel--shop">
    <p class="body-text" style="margin-top:20px">We make all our cupcakes with a little "bling" just to give them that sparkle that makes not only delicious to eat, but beautiful to see.</p>
    <div class="ribbon" style="font-size:22px;margin-top:8px;padding:2px 0">Our Cupcakes:</div>
    <ul class="list" style="margin-top:6px">
      <li>Baked Fresh Daily</li><li>Daily Specials Cupcakes</li><li>Unique Flavors</li><li>Catering for Parties and Events</li><li>Special Orders for Business Meetings and Weddings</li>
    </ul>
    <div class="ribbon" style="font-size:28px;margin-top:8px;padding:0">Gelato</div>
    <div style="display:flex;gap:8px;margin-top:6px;align-items:flex-start">
      <div class="photo" role="img" aria-label="Photo of pink gelato scoops" style="width:90px;height:80px;flex:none;background:linear-gradient(135deg,#f5d7e3,#e2708f)"></div>
      <p class="body-text" style="text-align:left">Gelato is Italian Ice Cream made with significantly less fat than traditional ice cream. Our gelato and sorbetto is made from scratch.</p>
    </div>
    <p class="body-text" style="margin-top:4px">Each batch of gelato and sorbetto is made to order fresh with authentic, Italian flavors and raw ingredients. Natural ingredients and fresh fruits are used in our Gelato and Sorbetto. Only the highest quality creams, fruits, nuts, spices, liqueurs, imported chocolates, coffees and teas are used. We invite everyone in the area to come in and try a few flavors to see what your favorite is before ordering.</p>
    <p class="body-text">Espresso/Cappuchino/Coffee Tea<br>If you want a great cup of coffee or tea, you have to stop in TPCH. We offer imported Italian Coffee and an Assortment of freshly brewed organic Tea.</p>
    <div class="contact-strip">Phone: 555-014-2290<br>www.PlumberryCakeHouse.com</div>
  </article>
</section>

<section class="sheet sheet--outside">
  <article class="panel panel--classes">
    <div class="band band--top"></div>
    <div class="ribbon" style="font-size:20px;line-height:1;margin-top:42px;padding:4px 0">Cake Decorating<br>Classes And Parties</div>
    <div style="display:flex;gap:8px;margin-top:8px;align-items:flex-start">
      <div class="icon-cupcake" role="img" aria-label="Cupcake illustration"></div>
      <p class="body-text">TPCH offers a variety of cake decorating classes. Whether you are an amateur who has never baked a cake, or a more advanced cake decorator, there is something for you in our selection of classes.</p>
    </div>
    <div style="display:flex;gap:4px;margin-top:8px">
      <div class="photo" role="img" aria-label="Photo of a cupcake with blue frosting" style="width:86px;height:86px;background:linear-gradient(160deg,#9cc7d8,#e8d7b2)"></div>
      <div class="photo" role="img" aria-label="Photo of a cupcake with sprinkles" style="width:86px;height:86px;background:linear-gradient(160deg,#f2eee0,#e6a24a)"></div>
      <div class="photo" role="img" aria-label="Photo of a chocolate frosted cupcake" style="width:86px;height:86px;background:linear-gradient(160deg,#6b3d2a,#d9a25a)"></div>
    </div>
    <p class="body-text" style="margin-top:12px">In our classes you will learn the best expert decorating techniques for cakes, cookies, cupcakes and cakepops.</p>
    <p class="body-text">All our classes are "hands-on," so when the class is over you will have a creation to take home to show and savor with your loved ones. We will use the same tools and methods as we do when making our own cakes in our shop.</p>
    <p class="body-text">Many of our sessions will be taught by a master cake decorator and culinary arts instructor.</p>
    <p class="body-text">Classes are conducted in small groups, allowing for personal attention to each student. You should reserve your place ahead of time to ensure a space</p>
    <div class="ribbon" style="position:absolute;left:16px;right:16px;bottom:14px;font-size:18px;line-height:1.05;padding:4px 0">Please call<br>for more details and the schedule.</div>
  </article>

  <article class="panel panel--location">
    <div class="band band--top"></div>
    <div class="logo" style="margin-top:46px"><span class="logo__dot"></span><span class="logo__name">The Plumberry Cake House</span></div>
    <div class="tagline-art" role="img" aria-label="Hand-lettered tagline" style="margin-top:10px"></div>
    <div style="margin-top:16px;width:92%;background:var(--white);border:2px solid var(--pink)">
      <div role="img" aria-label="Street map of the area around the shop" style="height:200px;background:linear-gradient(135deg,#d8e7cf,#eef1ea 45%,#8fc0e0)"></div>
      <div style="background:var(--pink-soft);padding:8px;font-size:10.5px;text-align:center;line-height:1.35;display:flex;align-items:center;gap:6px">
        <span style="flex:1">Located in Harbor Pines Center<br>4120 Harbor Pines Way<br>Bayview, Florida 33400</span>
        <div class="icon-cupcake" role="img" aria-label="Cupcake illustration" style="width:26px;height:30px"></div>
      </div>
      <div style="display:flex;font-size:11px;border-top:1px solid var(--grey)">
        <span style="flex:1;text-align:center;padding:6px 0;border-right:1px solid var(--grey)">Phone<br>555-014-2290</span>
        <span style="flex:1;display:flex;align-items:center;justify-content:center;gap:5px">
          <svg width="16" height="12" viewBox="0 0 16 12" aria-hidden="true"><g fill="none" stroke="#1b1b1b" stroke-width="1.6" stroke-linecap="round"><path d="M1 4.5a10 10 0 0 1 14 0"/><path d="M3.5 7a6.5 6.5 0 0 1 9 0"/></g><circle cx="8" cy="10" r="1.4" fill="#1b1b1b"/></svg>Free WiFi</span>
      </div>
      <div style="background:var(--pink-soft);font-size:11px;text-align:center;padding:6px 0">www.PlumberryCakeHouse.com</div>
    </div>
    <div class="band band--bottom"></div>
  </article>

  <article class="panel panel--cover">
    <div style="position:absolute;top:0;left:0;right:0;height:190px;background:linear-gradient(90deg,#f7c5dd,#fbe1ee,#f7c5dd)"></div>
    <div style="position:relative;margin-top:50px;width:236px;height:236px;border-radius:50%;background:var(--white);border:6px solid var(--pink-soft);box-shadow:0 0 0 2px var(--pink);display:flex;flex-direction:column;align-items:center;justify-content:center">
      <div class="logo" style="margin-top:0"><span class="logo__dot" style="width:11px;height:11px"></span><span class="logo__name" style="font-size:14px;letter-spacing:0">The Plumberry Cake House</span></div>
      <div class="tagline-art" role="img" aria-label="Hand-lettered tagline" style="margin-top:12px;width:170px;height:30px"></div>
    </div>
    <div style="position:relative;margin-top:34px;width:88%;background:var(--white);border:3px solid var(--pink-soft);text-align:center;padding:10px 0 0">
      <div class="icon-cupcake" role="img" aria-label="Cupcake illustration" style="position:absolute;right:-10px;top:-26px"></div>
      <p class="script" style="font-size:26px;color:var(--pink-deep)">Hours</p>
      <p style="font-size:12px;line-height:1.45">Monday:<br>By Appointment<br>Tuesday-Thursday: 11-7<br>Friday: 11-10<br>Saturday: 10-10<br>Sunday: 11-7</p>
      <div style="margin-top:10px;background:var(--pink-deep);color:var(--white);font-size:11px;padding:6px 0;line-height:1.4">www.plumberrycakehouse.com<br>phone: 555-014-2290</div>
    </div>
  </article>
</section>

</body>
</html>
```